Velmaro Partners Logo and Business Card Design

We already have the rough logo shape (however please make the lines on the logo much thicker so a dark background is not required to see it) . see photos uploaded.
It needs to be refined with color and digitized and then have a front and back business card layout done.
The services are high vibration healing support through a therapy and feng shui service offering. We want people to Feel Happiness, Feel Prosperity and Feel Peace. (the back of the card would have these phrases on it) So a warm, calm and peaceful feeling card.
We would like the card to use the logo provided (with thicker lines and color added) but below the graphic please use the name "Velmaro Partners" NOT Velmaro.
We also would like to use the colors in the colorized matrix shown in photos (gold and purple) but on the lighter side. Thanks for your time!

Front of Card should include: Logo, with Company Name: Velmaro Partners as part of logo, Name: Tomas Brekke email: tomas@velmaro.example web: www.velmaro.example mobile: 555.018.2264 at bottom of front list Family Constellation | Feng Shui

Back of Card should have the logo and the following listed vertically:

PERSONAL | BUSINESS (Larger size then smaller bullet items below)
*Find Happiness
*Find Prosperity
*Find Peace

Target Market(s)

Target market is both business and personal

Contact Information for Business Card

Front of Card should include: Logo, with Company Name: Velmaro Partners as part of logo, Name: Tomas Brekke email: tomas@velmaro.example web: www.velmaro.example mobile: 555.018.2264 at bottom of front list Family Constellation | Feng Shui ++++ Back of Card should have the logo and the following listed vertically: PERSONAL | BUSINESS (Larger size then smaller bullet items below) *Find Happiness *Find Prosperity *Find Peace

Font styles to use
Sans Serif

Colors

Designer to choose colors to be used in the design.

Requirements
Nice to have
• Nice light contrast color for the back of card background
Should not have
• No dark colored background on Card.

```html
<!DOCTYPE html>
<html lang="en">
<head>
<meta charset="utf-8">
<title>Velmaro Partners – Business Card</title>
<link rel="stylesheet" href="https://fonts.googleapis.com/css2?family=Bebas+Neue&family=Lora:ital,wght@0,400;0,600;1,400;1,500&family=Montserrat:wght@400;600&display=swap">
<style>
  :root {
    --stage: #ababab;
    --card: #f9f1e3;
    --purple: #8e4a9a;
    --gold: #a8862f;
    --gold-soft: #c9ad63;
    --grey: #7b7b74;
    --rule: #cfc3b0;
  }
  * { margin: 0; padding: 0; box-sizing: border-box; }
  html, body { width: 1200px; height: 1000px; overflow: hidden; }
  body { background: var(--stage); position: relative; font-family: "Montserrat", sans-serif; }

  .card {
    position: absolute; left: 294px; width: 613px; height: 352px;
    background: var(--card); border-radius: 24px;
    box-shadow: 0 18px 40px rgba(0,0,0,0.28);
  }
  .card--front { top: 118px; }
  .card--back { top: 530px; }

  .brand { position: absolute; text-align: center; }
  .brand__mark { display: block; margin: 0 auto; }
  .brand__name {
    font-family: "Lora", serif; font-weight: 600; color: var(--purple);
    line-height: 1.1; white-space: nowrap;
  }
  .card--front .brand { left: 58px; top: 88px; width: 200px; }
  .card--front .brand__name { font-size: 26px; margin-top: 18px; }
  .card--back .brand { left: 336px; top: 92px; width: 230px; }
  .card--back .brand__name { font-size: 29px; margin-top: 20px; }

  .contact { position: absolute; left: 330px; top: 96px; width: 200px; text-align: center; }
  .contact__name { font-family: "Lora", serif; font-style: italic; font-size: 34px; color: var(--purple); line-height: 1; margin-bottom: 22px; }
  .contact__line { font-size: 17px; color: var(--grey); line-height: 23px; white-space: nowrap; }
  .contact__phone { font-size: 20px; font-weight: 600; color: var(--grey); margin-top: 10px; white-space: nowrap; }

  .card__rule { position: absolute; left: 14px; right: 14px; top: 311px; border-top: 1px solid var(--rule); }
  .services {
    position: absolute; left: 0; right: 0; top: 318px; text-align: center;
    font-family: "Lora", serif; font-size: 17px; letter-spacing: 0.6px; color: var(--purple);
  }

  .offer { position: absolute; left: 56px; top: 110px; }
  .offer__heading {
    display: inline-block; font-family: "Bebas Neue", sans-serif; font-size: 25px;
    letter-spacing: 1.5px; color: var(--gold); border-bottom: 1px solid var(--gold);
    line-height: 1; padding-bottom: 1px; margin-bottom: 16px;
  }
  .offer__list { list-style: none; }
  .offer__item { font-family: "Lora", serif; font-style: italic; font-weight: 500; font-size: 30px; color: var(--purple); line-height: 36px; white-space: nowrap; }
</style>
</head>
<body>

<section class="card card--front">
  <div class="brand">
    <svg class="brand__mark" width="66" height="66" viewBox="0 0 66 66" aria-hidden="true">
      <circle cx="33" cy="33" r="29" fill="none" stroke="var(--gold-soft)" stroke-width="5"/>
    </svg>
    <div class="brand__name">Velmaro Partners</div>
  </div>

  <div class="contact">
    <h1 class="contact__name">Tomas Brekke</h1>
    <p class="contact__line">tomas@velmaro.example</p>
    <p class="contact__line">www.velmaro.example</p>
    <p class="contact__phone">555.018.2264</p>
  </div>

  <div class="card__rule"></div>
  <p class="services">Family Constellation &nbsp;|&nbsp; Feng Shui</p>
</section>

<section class="card card--back">
  <div class="offer">
    <h2 class="offer__heading">Personal &nbsp;|&nbsp; Business</h2>
    <ul class="offer__list">
      <li class="offer__item">*Find Happiness</li>
      <li class="offer__item">*Find Prosperity</li>
      <li class="offer__item">*Find Peace</li>
    </ul>
  </div>

  <div class="brand">
    <svg class="brand__mark" width="76" height="76" viewBox="0 0 76 76" aria-hidden="true">
      <circle cx="38" cy="38" r="34" fill="none" stroke="var(--gold-soft)" stroke-width="5"/>
    </svg>
    <div class="brand__name">Velmaro Partners</div>
  </div>
</section>

</body>
</html>
```